Weekly Newsletter template for our niche within the Telecom Industry

We need a 'skeleton' format where we can insert our weekly information and ads.
We will do all the content in-house.
Content in both info and ads must be able to contain hyperlinks.
Our company website is: www. halvorsen-quibb.com
We think we would like something similar to the top format but with the single bar on the right side as a place to insert ads
Thank you.

```html
<!DOCTYPE html>
<html lang="en">
<head>
<meta charset="utf-8">
<title>Halvorsen Quibb – Weekly Newsletter</title>
<link href="https://fonts.googleapis.com/css2?family=Poppins:wght@300;400;500;600;700&display=swap" rel="stylesheet">
<style>
  :root {
    --canvas: #ebebeb;
    --paper: #ffffff;
    --ink: #2b2d2f;
    --dark: #2d2f31;
    --teal: #1fb5d1;
    --teal-soft: #e3f3f9;
    --lime: #a9c64a;
    --muted: #5a5d60;
  }
  * { box-sizing: border-box; margin: 0; padding: 0; }
  html, body { width: 901px; height: 1200px; overflow: hidden; }
  body {
    background: var(--canvas);
    font-family: "Poppins", sans-serif;
    color: var(--ink);
    position: relative;
  }
  a { color: inherit; text-decoration: none; }

  .page {
    position: absolute;
    left: 256px;
    width: 390px;
    height: 552px;
    background: var(--paper);
    box-shadow: 0 2px 8px rgba(0,0,0,0.12);
    overflow: hidden;
  }
  .page--cover { top: 43px; }
  .page--inner { top: 611px; }

  /* masthead */
  .masthead {
    position: absolute; left: 0; top: 0; width: 390px; height: 166px;
    background: var(--dark);
  }
  .masthead__backdrop {
    position: absolute; left: 0; top: 0; width: 226px; height: 166px;
    background: radial-gradient(ellipse at 70% 30%, #4a5358 0%, #33383b 45%, var(--dark) 80%);
  }
  .masthead__text { position: absolute; left: 26px; top: 26px; }
  .volume-tag {
    display: inline-block; background: var(--teal); color: #fff;
    font-size: 11.5px; font-weight: 400; line-height: 16px; padding: 0 5px;
  }
  .masthead__title {
    color: #fff; font-weight: 600; font-size: 24.5px; line-height: 27px;
    margin-top: 6px; letter-spacing: 0.2px;
  }
  .masthead__subtitle {
    color: var(--teal); font-weight: 300; font-size: 13px; line-height: 14px; margin-top: 1px;
  }

  /* left column */
  .article {
    position: absolute; left: 26px; top: 190px; width: 186px;
  }
  .page--inner .article { top: 19px; }
  .accent-bar {
    width: 40px; height: 3px;
    background: linear-gradient(90deg, var(--teal), var(--lime));
  }
  .article__heading {
    font-size: 15.5px; font-weight: 500; line-height: 16px; margin-top: 9px;
    letter-spacing: -0.1px;
  }
  .sub-heading {
    font-size: 7.4px; font-weight: 600; line-height: 9px; margin-top: 11px; letter-spacing: 0.1px;
  }
  .body-copy { font-size: 6.6px; line-height: 7.9px; margin-top: 2px; }
  .body-copy--dense { line-height: 7.9px; }
  .body-copy--strong { font-weight: 600; margin-top: 4px; }
  .pull-quote {
    border-top: 1px solid var(--teal); border-bottom: 1px solid var(--teal);
    color: var(--teal); font-weight: 600; font-size: 6.6px; line-height: 7.9px;
    padding: 6px 0 6px; margin-top: 8px;
  }
  .checklist { list-style: none; margin-top: 8px; }
  .checklist li {
    font-size: 6.6px; line-height: 10.5px; display: flex; align-items: center; gap: 6px;
  }
  .checklist svg { width: 6px; height: 6px; flex: none; }
  .site-link {
    position: absolute; left: 26px; top: 533px; font-size: 4.6px; color: var(--muted);
    display: flex; align-items: center; gap: 3px;
  }
  .site-link svg { width: 6px; height: 6px; }

  /* right column */
  .sidebar { position: absolute; left: 226px; width: 164px; }
  .brand-box {
    top: 42px; height: 53px; background: #fff;
    display: flex; align-items: center; justify-content: center; gap: 8px;
  }
  .brand-box__mark { width: 10px; height: 10px; border-radius: 50%; background: var(--teal); }
  .brand-box__name { font-size: 12px; font-weight: 500; color: var(--ink); letter-spacing: 0.3px; }

  .ad-panel { padding: 7px 13px 0; }
  .ad-panel__heading { font-size: 12.5px; font-weight: 600; line-height: 16px; }
  .ad-panel__copy { font-size: 6.6px; line-height: 10.5px; margin-top: 1px; }
  .ad-panel--teal { background: var(--teal); color: #fff; top: 96px; height: 183px; }
  .ad-panel--teal .ad-panel__heading { margin-top: 0; }
  .ad-panel--dark { background: var(--dark); color: #fff; top: 0; height: 153px; padding-top: 16px; }
  .ad-panel--light { background: var(--teal-soft); color: var(--ink); top: 276px; height: 139px; padding-top: 9px; }
  .ad-panel--dark .ad-panel__copy, .ad-panel--light .ad-panel__copy { line-height: 7.9px; margin-top: 4px; }

  .ad-photo { }
  .ad-photo--network {
    background: radial-gradient(circle at 50% 38%, #9fe6ff 0%, #2f9fe0 14%, #0d5ea6 40%, #0a2f55 80%);
  }
  .ad-photo--tower {
    background: radial-gradient(circle at 30% 45%, #dbe7fb 0%, #a9c4f0 45%, #7ea2dc 100%);
  }
  .photo-cover-1 { top: 282px; height: 119px; }
  .photo-cover-2 { top: 404px; height: 148px; }
  .photo-inner-1 { top: 155px; height: 119px; }
  .photo-inner-2 { top: 418px; height: 134px; }

  .read-more {
    position: absolute; right: 0; bottom: 0; width: 48px; height: 10px;
    font-size: 5px; line-height: 10px; text-align: center; color: #fff;
  }
  .read-more--dark { background: var(--dark); }
  .read-more--teal { background: var(--teal); }
</style>
</head>
<body>

<section class="page page--cover">
  <header class="masthead">
    <div class="masthead__backdrop" role="img" aria-label="Faint network globe over a night city skyline"></div>
    <div class="masthead__text">
      <span class="volume-tag">Volume 01</span>
      <h1 class="masthead__title">YOUR<br>COMPANY<br>NEWS LETTER</h1>
      <p class="masthead__subtitle">WEEKLY UPDATE</p>
    </div>
  </header>

  <article class="article">
    <div class="accent-bar"></div>
    <h2 class="article__heading">This is Heading This is Heading</h2>
    <h3 class="sub-heading">THIS IS SUB HEADING</h3>
    <p class="body-copy">Iliquiat urepedi volorrovitia voluptae perovita volupti usdant verum dit dolest laciam eria sent ra doluptaspit rerferum repudip icium, simporiorem rem evel invendigene diae nusa sim quate nis ditatibus samus</p>
    <p class="body-copy body-copy--strong">excessus voluptae verum fugit ipsapit ute volo mo tore sitatendit alicius doluptaqui doluptatio.</p>
    <p class="body-copy">usdant verum dit dolest laciam eria sent ra doluptaspit rerferum repudip icium, simporiorem rem evel</p>
    <p class="body-copy body-copy--strong">excessus voluptae verum fugit ipsapit ute volo mo tore sitatendit alicius doluptaqui doluptatio.</p>
    <p class="body-copy">usdant verum dit dolest laciam eria sent ra doluptaspit rerferum repudip icium, simporiorem rem evel</p>
    <p class="pull-quote">usdant verum dit dolest laciam eria sent ra doluptaspit rerferum repudip icium, simporiorem rem evel</p>
    <h3 class="sub-heading">THIS IS SUB HEADING</h3>
    <p class="body-copy">Iliquiat urepedi volorrovitia voluptae perovita volupti usdant verum dit dolest laciam eria sent ra doluptaspit rerferum repudip icium, simporiorem rem evel</p>
    <h3 class="sub-heading">THIS IS SUB HEADING</h3>
    <p class="body-copy" style="line-height:9px;margin-top:3px">Et maximinis as della et aut et quia doluptae quis molendi tiuntur,</p>
    <ul class="checklist">
      <li><svg viewBox="0 0 10 10"><circle cx="5" cy="5" r="5" fill="#1fb5d1"/><path d="M2.8 5.2l1.5 1.5 3-3" stroke="#fff" stroke-width="1.2" fill="none"/></svg>Verempo reptatet: magnis asi cus alitas</li>
      <li><svg viewBox="0 0 10 10"><circle cx="5" cy="5" r="5" fill="#1fb5d1"/><path d="M2.8 5.2l1.5 1.5 3-3" stroke="#fff" stroke-width="1.2" fill="none"/></svg>Verempo reptatet: magnis asi cus alitas</li>
    </ul>
  </article>

  <a class="site-link" href="https://www.halvorsen-quibb.com">
    <svg viewBox="0 0 12 12"><circle cx="6" cy="6" r="5.2" fill="none" stroke="#1fb5d1" stroke-width="1"/><ellipse cx="6" cy="6" rx="2.2" ry="5.2" fill="none" stroke="#1fb5d1" stroke-width="0.8"/><path d="M0.8 6h10.4" stroke="#1fb5d1" stroke-width="0.8"/></svg>
    www. halvorsen-quibb.com
  </a>

  <div class="sidebar brand-box">
    <span class="brand-box__mark"></span>
    <span class="brand-box__name">HALVORSEN QUIBB</span>
  </div>

  <aside class="sidebar ad-panel ad-panel--teal">
    <h2 class="ad-panel__heading">Hedding</h2>
    <p class="ad-panel__copy">explabora corehenda dolum si occatem accum nim rae velitibus et reped qui ommo optati simusa quam de dolessi bla verrore mpore, que nonse exerit autat estiunt andelestis voluptamus dunt excerios aut ommolest Citaerferrunt ad ut laturit emolore henestias doluptam ipid utemquae et fuga. Ut et a et evelit labo. Enisti ra cus eaque perem que preratqui ad ut eum faccabo. Tis est porum essinte necus.<br>Usa volut quam lautaquibus et, sectore vel inihil ipis exercit</p>
    <a class="read-more read-more--dark" href="#">Read More...</a>
  </aside>

  <div class="sidebar ad-photo ad-photo--network photo-cover-1" role="img" aria-label="Hand touching a glowing AI network interface">
    <a class="read-more read-more--dark" href="#">Read More...</a>
  </div>
  <div class="sidebar ad-photo ad-photo--tower photo-cover-2" role="img" aria-label="Telecom tower with signal waves against a blue sky">
    <a class="read-more read-more--teal" href="#">Read More...</a>
  </div>
</section>

<section class="page page--inner">
  <article class="article">
    <div class="accent-bar"></div>
    <h2 class="article__heading">This is Heading This is Heading</h2>
    <h3 class="sub-heading">THIS IS SUB HEADING</h3>
    <p class="body-copy">Iliquiat urepedi volorrovitia voluptae perovita volupti usdant verum dit dolest laciam eria sent ra doluptaspit rerferum repudip icium, simporiorem rem evel invendigene diae nusa sim quate nis</p>
    <h3 class="sub-heading" style="margin-top:3px">THIS IS SUB HEADING</h3>
    <p class="body-copy" style="line-height:9px;margin-top:3px">Et maximinis as della et aut et quia doluptae quis molendi tiuntur,</p>
    <ul class="checklist">
      <li><svg viewBox="0 0 10 10"><circle cx="5" cy="5" r="5" fill="#1fb5d1"/><path d="M2.8 5.2l1.5 1.5 3-3" stroke="#fff" stroke-width="1.2" fill="none"/></svg>Verempo reptatet: magnis asi cus alitas</li>
      <li><svg viewBox="0 0 10 10"><circle cx="5" cy="5" r="5" fill="#1fb5d1"/><path d="M2.8 5.2l1.5 1.5 3-3" stroke="#fff" stroke-width="1.2" fill="none"/></svg>Verempo reptatet: magnis asi cus alitas</li>
    </ul>
    <h3 class="sub-heading" style="margin-top:20px">THIS IS SUB HEADING</h3>
    <p class="body-copy">Iliquiat urepedi volorrovitia voluptae perovita volupti usdant verum dit dNam incidem rem ario. Uptat unti aut labori blam quam que restiorro odis doluptibus eost, officiusdam reicatio ilis excearc hillam hilitatem dit maxim venient adiae esciam sit voluptature sunt, con conseca esecto optae dolo conem et aut voluptaspid enis dolorum rernatiist maio modis et eumquide quunt qui ulpa voluptur arion prerios doluptatur accullum quiae officimet ulpa quas aute pos aut vel ipsam nobis mo quo blaccum dolupta volum in everiat officius moloreptatur adipient omnisim aximin pre occum quid quas as dolenducia verferat volorem poribus cipsum ipit,</p>
    <h3 class="sub-heading" style="margin-top:20px">THIS IS SUB HEADING</h3>
    <p class="body-copy">Iliquiat urepedi volorrovitia voluptae perovita volupti usdant verum dit dNam incidem rem ario. Uptat unti aut labori blam quam que restiorro odis doluptibus eost, officiusdam reicatio ilis excearc hillam hilitatem dit maxim venient adiae esciam sit voluptature sunt, con conseca esecto optae dolo conem et aut voluptaspid enis dolorum rernatiist maio modis et eumquide quunt qui ulpa voluptur arion prerios doluptatur accullum quiae officimet ulpa quas aute pos aut vel ipsam nobis mo quo blaccum dolupta volum in everiat officius moloreptatur adipient omnisim aximin pre occum quid quas as dolenducia verferat volorem poribus cipsum ipit,</p>
    <h3 class="sub-heading" style="margin-top:17px">THIS IS SUB HEADING</h3>
    <p class="body-copy" style="line-height:9px;margin-top:3px">Et maximinis as della et aut et quia doluptae quis molendi tiuntur,</p>
    <ul class="checklist">
      <li><svg viewBox="0 0 10 10"><circle cx="5" cy="5" r="5" fill="#1fb5d1"/><path d="M2.8 5.2l1.5 1.5 3-3" stroke="#fff" stroke-width="1.2" fill="none"/></svg>Verempo reptatet: magnis asi cus alitas</li>
      <li><svg viewBox="0 0 10 10"><circle cx="5" cy="5" r="5" fill="#1fb5d1"/><path d="M2.8 5.2l1.5 1.5 3-3" stroke="#fff" stroke-width="1.2" fill="none"/></svg>Verempo reptatet: magnis asi cus alitas</li>
      <li><svg viewBox="0 0 10 10"><circle cx="5" cy="5" r="5" fill="#1fb5d1"/><path d="M2.8 5.2l1.5 1.5 3-3" stroke="#fff" stroke-width="1.2" fill="none"/></svg>Verempo reptatet: magnis asi cus alitas</li>
      <li><svg viewBox="0 0 10 10"><circle cx="5" cy="5" r="5" fill="#1fb5d1"/><path d="M2.8 5.2l1.5 1.5 3-3" stroke="#fff" stroke-width="1.2" fill="none"/></svg>Verempo reptatet: magnis asi cus alitas</li>
    </ul>
  </article>

  <aside class="sidebar ad-panel ad-panel--dark">
    <h2 class="ad-panel__heading">Hedding</h2>
    <p class="ad-panel__copy">explabora corehenda dolum si occatem accum nim rae velitibus et reped qui ommo optati simusa quam de dolessi bla verrore mpore, que nonse exerit autat estiunt andelestis voluptamus dunt excerios aut ommolest Citaerferrunt ad ut laturit emolore henestias doluptam ipid utemquae et fuga. Ut et a et evelit labo. Enisti ra cus eaque perem que preratqui ad ut eum faccabo. Tis est porum essinte necus. Usa volut quam lautaquibus et, sectore vel inihil ipis exercit</p>
    <a class="read-more read-more--teal" href="#">Read More...</a>
  </aside>

  <div class="sidebar ad-photo ad-photo--network photo-inner-1" role="img" aria-label="Hand touching a glowing AI network interface">
    <a class="read-more read-more--dark" href="#">Read More...</a>
  </div>

  <aside class="sidebar ad-panel ad-panel--light">
    <h2 class="ad-panel__heading">Hedding</h2>
    <p class="ad-panel__copy">explabora corehenda dolum si occatem accum nim rae velitibus et reped qui ommo optati simusa quam de dolessi bla verrore mpore, que nonse exerit autat estiunt andelestis voluptamus dunt excerios aut ommolest Citaerferrunt ad ut laturit emolore henestias doluptam ipid utemquae et fuga. Ut et a et evelit labo. Enisti ra cus eaque perem que preratqui ad ut eum faccabo. Tis est porum essinte necus. Usa volut quam lautaquibus et, sectore vel inihil ipis exercit</p>
    <a class="read-more read-more--teal" href="#">Read More...</a>
  </aside>

  <div class="sidebar ad-photo ad-photo--network photo-inner-2" role="img" aria-label="Hand touching a glowing AI network interface">
    <a class="read-more read-more--teal" href="#">Read More...</a>
  </div>
</section>

</body>
</html>
```